Business Card Design for Marketing Firm

Looking for business card design for higher end marketing firm. Clean but impressionable/trendy. We are a marketing firm that represents manufacturers in the foodservice equipment and supply industry. Our customers are end users such has hotels, restaurants, country clubs, convention centers and casinos as well as distributors of restaurants supplies and equipment, and manufacturers of foodservice equipment and supplies.
Target Market(s)
Hotels, Restaurants, Supply & Equipment Distributors, Foodservice Manufacturers
Industry/Entity Type
Foodservice/Hospitality
Contact Information for Business Card
Name, Title, Contact Number, Email, Website, Social Media, Address
Requirements
Must have
- Clean & Simple but Serious and Impressionable

```html
<!DOCTYPE html>
<html lang="en">
<head>
<meta charset="utf-8">
<title>Harbor Hospitality Reps – Business Card</title>
<link rel="stylesheet" href="https://fonts.googleapis.com/css2?family=Montserrat:wght@400;500;600&display=swap">
<style>
  :root {
    --navy: #17158a;
    --navy-soft: #2a2a9e;
    --lilac: #8e8cf0;
    --ink: #5a5a66;
    --paper: #ffffff;
    --backdrop: #e9e9ee;
  }
  * { box-sizing: border-box; margin: 0; padding: 0; }
  html, body { width: 1200px; height: 987px; overflow: hidden; }
  body {
    background: var(--backdrop);
    font-family: "Montserrat", sans-serif;
    position: relative;
  }
  .card {
    position: absolute;
    left: 250px;
    width: 700px;
    height: 400px;
    border-radius: 4px;
    overflow: hidden;
    box-shadow: 0 6px 18px rgba(0,0,0,.18);
  }
  /* Reverse side */
  .card-back { top: 50px; background: var(--navy); }
  .card-back .pattern {
    position: absolute; inset: 0;
    background: linear-gradient(135deg, var(--navy-soft) 0%, var(--navy) 70%);
  }
  .card-back .brand-mark {
    position: absolute;
    left: 470px; top: 188px;
    color: var(--paper);
    font-weight: 600;
    font-size: 15px;
    letter-spacing: .5px;
  }
  /* Front side */
  .card-front { top: 510px; background: var(--paper); }
  .brand {
    position: absolute;
    left: 40px; top: 140px;
    width: 330px;
    text-align: center;
    color: var(--navy);
    font-weight: 600;
  }
  .brand-name { font-size: 22px; letter-spacing: 1px; }
  .brand-sub { font-size: 13px; letter-spacing: 3px; margin-top: 4px; }
  .brand-dot {
    display: inline-block; width: 10px; height: 10px;
    background: var(--navy); border-radius: 50%;
    margin-bottom: 14px;
  }
  .divider {
    position: absolute; left: 395px; top: 70px;
    width: 2px; height: 190px; background: var(--navy);
  }
  .contact { position: absolute; left: 420px; top: 72px; color: var(--ink); }
  .person-name { color: var(--navy); font-weight: 600; font-size: 22px; }
  .person-title { font-size: 14px; margin-bottom: 16px; }
  .address { font-size: 14px; line-height: 1.3; margin-bottom: 14px; }
  .line { display: flex; align-items: center; gap: 8px; font-size: 14px; line-height: 1.5; }
  .line svg { width: 13px; height: 13px; fill: var(--navy); }
  .footer { position: absolute; left: 0; bottom: 0; width: 700px; height: 130px; }
  .social {
    position: absolute; right: 22px; top: 302px;
    color: var(--paper); font-size: 15px; line-height: 1;
    display: flex; align-items: center; gap: 7px;
  }
  .social .square { width: 14px; height: 14px; background: var(--paper); border-radius: 2px; }
</style>
</head>
<body>
  <section class="card card-back">
    <div class="pattern" role="img" aria-label="Repeated script monogram pattern in tone-on-tone navy"></div>
    <span class="brand-mark">Harbor</span>
  </section>

  <section class="card card-front">
    <div class="brand">
      <span class="brand-dot"></span>
      <div class="brand-name">HARBOR HOSPITALITY</div>
      <div class="brand-sub">REPS</div>
    </div>

    <div class="divider"></div>

    <div class="contact">
      <div class="person-name">Dana Reyes</div>
      <div class="person-title">President</div>
      <div class="address">Street Name Avenue, Suite 100<br>State, Zip Code, Country</div>
      <div class="line">
        <svg viewBox="0 0 16 16"><path d="M3 1l3 3-1.5 2a9 9 0 0 0 5.5 5.5L12 10l3 3-2 2C6 15 1 10 1 3z"/></svg>
        012-345-6789
      </div>
      <div class="line">
        <svg viewBox="0 0 16 16"><path d="M1 3h14v10H1z M1 3l7 6 7-6" stroke="#fff" stroke-width="1"/></svg>
        info@yourwebsitehere.com
      </div>
      <div class="line">
        <svg viewBox="0 0 16 16"><circle cx="8" cy="8" r="7" fill="none" stroke="#17158a" stroke-width="1.5"/><path d="M1 8h14M8 1v14" stroke="#17158a" stroke-width="1.2"/></svg>
        yourwebsitehere.com
      </div>
    </div>

    <svg class="footer" viewBox="0 0 700 130" aria-hidden="true">
      <path d="M0 92 L462 58 L474 65 L0 102 Z" fill="var(--lilac)"/>
      <path d="M0 102 L474 65 C505 60 515 26 548 21 L700 15 V130 H0 Z" fill="var(--navy)"/>
    </svg>
    <div class="social"><span class="square"></span>socialhandle</div>
  </section>
</body>
</html>
```